Bridgeway Health of Nations

Please design a business card that is colorful but at the same time easy to read. We are based out on Miami Florida. We are a small start up healthcare company that has been in operation for 1 year. Our clients are Hospitals, Insurance companies, and Manage Care health companies. We are growing quickly and lead the niche we are in. Please make the card 2 sided on the front will be the typical info. Logo, Company Name, Persons Name, Title, Cell #, Office #, Fax#, email, website. No address. On the back we will list 5 services that we do. For example Care Transitions, Case management, Risk assessment, Utilization Review.
Target Market(s)
CEO's and COO's of hospitals and healthcare companies.
Industry/Entity Type
Healthcare

```html
<!DOCTYPE html>
<html lang="en">
<head>
<meta charset="utf-8">
<title>Bridgeway Health of Nations – Business Card</title>
<link rel="stylesheet" href="https://fonts.googleapis.com/css2?family=Lato:ital,wght@0,400;0,700;0,900;1,700&display=swap">
<style>
  :root {
    --backdrop: #5a5c60;
    --card-white: #f7f7f5;
    --band-blue: #1d4fa3;
    --band-blue-deep: #153d86;
    --name-green: #22a236;
    --label-blue: #1d4fa3;
    --ink: #1c1c1c;
    --card-dark: #262729;
    --strip-dark: #1b1c1e;
    --service-blue: #2a8ad6;
    --mark-navy: #2f3d9a;
  }
  * { box-sizing: border-box; margin: 0; padding: 0; }
  html, body { width: 1200px; height: 926px; overflow: hidden; }
  body {
    background: var(--backdrop);
    font-family: "Lato", sans-serif;
    position: relative;
  }
  .card {
    position: absolute;
    left: 250px;
    width: 700px;
    height: 400px;
    border-radius: 4px;
    overflow: hidden;
    box-shadow: 0 10px 28px rgba(0,0,0,.35);
  }

  /* Front */
  .card--front { top: 46px; background: var(--card-white); }
  .front__band {
    height: 78px;
    background: linear-gradient(90deg, var(--band-blue-deep), var(--band-blue));
    display: flex;
    align-items: center;
    padding-left: 40px;
  }
  .front__company {
    color: #fff;
    font-size: 28px;
    font-weight: 700;
    letter-spacing: 1px;
  }
  .front__company small { font-size: 22px; font-weight: 400; text-transform: none; }
  .front__person { position: absolute; left: 40px; top: 118px; }
  .person__name { color: var(--name-green); font-size: 34px; font-weight: 400; }
  .person__name b { font-weight: 900; }
  .person__title { color: var(--ink); font-size: 17px; font-weight: 900; margin-left: 4px; }
  .contact-list { list-style: none; margin-top: 14px; margin-left: 8px; }
  .contact-list li { color: var(--ink); font-size: 19px; line-height: 27px; }
  .contact-list .label { color: var(--label-blue); font-weight: 700; font-style: italic; }
  .front__mark-space {
    position: absolute;
    right: 64px;
    top: 150px;
    width: 180px;
    height: 180px;
    border-radius: 50%;
    background: var(--mark-navy);
  }

  /* Back */
  .card--back { top: 480px; background: var(--card-dark); }
  .back__brand {
    position: absolute;
    top: 86px;
    left: 0; right: 0;
    display: flex;
    align-items: center;
    justify-content: center;
    gap: 22px;
  }
  .brand__dot { width: 64px; height: 64px; border-radius: 50%; background: var(--mark-navy); }
  .brand__name { color: #8b8c90; font-size: 38px; font-weight: 900; line-height: 1.1; }
  .back__services {
    position: absolute;
    left: 0; right: 0;
    top: 262px;
    height: 86px;
    background: var(--strip-dark);
    display: flex;
    align-items: center;
    justify-content: center;
    text-align: center;
    padding: 0 40px;
    color: var(--service-blue);
    font-size: 18px;
    letter-spacing: 1.5px;
    line-height: 1.45;
    text-transform: uppercase;
  }
</style>
</head>
<body>
  <section class="card card--front" aria-label="Business card front">
    <header class="front__band">
      <h1 class="front__company">BRIDGEWAY HEALTH <small>of</small> NATIONS</h1>
    </header>
    <div class="front__person">
      <h2 class="person__name">Daniel <b>Reyes</b><span class="person__title">-TITLE</span></h2>
      <ul class="contact-list">
        <li><span class="label">cell:</span> 123-456-7890</li>
        <li><span class="label">office:</span> 098-765-4321</li>
        <li><span class="label">fax:</span> 123-098-4567</li>
        <li><span class="label">email:</span> yourdomain.com</li>
        <li><span class="label">web:</span> yourname@yourdomain.com</li>
      </ul>
    </div>
    <div class="front__mark-space" aria-hidden="true"></div>
  </section>

  <section class="card card--back" aria-label="Business card back">
    <div class="back__brand">
      <span class="brand__dot" aria-hidden="true"></span>
      <p class="brand__name">Bridgeway Health<br>of Nations</p>
    </div>
    <p class="back__services">Care transitions, case management,<br>risk assessment, utilization review and manage care</p>
  </section>
</body>
</html>
```